SaaS Early tech startup business card design

Unique design for experience ecommerce platform company. the business cards will be used by executive members. conformance with color code is required.

```html
<!DOCTYPE html>
<html lang="en">
<head>
<meta charset="UTF-8">
<title>Velora Business Card</title>
<link rel="stylesheet" href="https://fonts.googleapis.com/css2?family=Arimo:wght@400;700&display=swap">
<style>
  :root {
    --page-bg: #2a2a2e;
    --card-navy: #1f1d38;
    --card-navy-light: #2a2847;
    --teal: #18b79a;
    --teal-bright: #27c6a8;
    --ocean: #1a7fa3;
    --text-white: #f2f2f6;
    --divider: #c9c9d6;
  }
  * { margin: 0; padding: 0; box-sizing: border-box; }
  html, body {
    width: 1200px;
    height: 900px;
    overflow: hidden;
    background: var(--page-bg);
    font-family: "Arimo", Arial, sans-serif;
  }
  .sheet {
    width: 1200px;
    height: 900px;
    display: flex;
    flex-direction: column;
    align-items: center;
    justify-content: center;
    gap: 40px;
  }
  .card {
    position: relative;
    width: 640px;
    height: 366px;
    border-radius: 22px;
    background: linear-gradient(135deg, var(--card-navy) 0%, var(--card-navy) 60%, var(--card-navy-light) 100%);
    overflow: hidden;
    box-shadow: 0 10px 30px rgba(0,0,0,0.35);
  }
  .brand-name {
    font-family: "Arimo", Arial, sans-serif;
    font-weight: 700;
    color: var(--teal);
    letter-spacing: 1px;
    line-height: 1;
  }
  .card-front {
    display: flex;
    align-items: center;
    justify-content: center;
  }
  .card-front .brand-name { font-size: 96px; }

  .card-back .swoosh {
    position: absolute;
    inset: 0;
  }
  .card-back .brand-name {
    position: absolute;
    left: 0; right: 0;
    top: 92px;
    text-align: center;
    font-size: 78px;
  }
  .person {
    position: absolute;
    right: 340px;
    top: 244px;
    text-align: right;
  }
  .person-name {
    font-size: 26px;
    font-weight: 700;
    color: var(--teal);
    white-space: nowrap;
  }
  .person-title {
    margin-top: 4px;
    font-size: 17px;
    color: var(--text-white);
  }
  .divider {
    position: absolute;
    left: 320px;
    top: 236px;
    width: 2px;
    height: 64px;
    background: var(--divider);
  }
  .contact-list {
    position: absolute;
    left: 340px;
    top: 236px;
    list-style: none;
    display: flex;
    flex-direction: column;
    gap: 5px;
  }
  .contact-item {
    display: flex;
    align-items: center;
    gap: 9px;
    font-size: 15px;
    color: var(--text-white);
    white-space: nowrap;
  }
  .contact-icon {
    width: 18px;
    height: 18px;
    flex: none;
  }
  .address {
    position: absolute;
    left: 0; right: 0;
    top: 320px;
    text-align: center;
    font-size: 17px;
    color: var(--text-white);
    letter-spacing: 0.3px;
  }
</style>
</head>
<body>
<main class="sheet">

  <section class="card card-front" aria-label="Card front">
    <span class="brand-name">velora</span>
  </section>

  <section class="card card-back" aria-label="Card back">
    <svg class="swoosh" width="640" height="366" viewBox="0 0 640 366" aria-hidden="true">
      <defs>
        <linearGradient id="swooshGrad" x1="0" y1="0" x2="1" y2="0">
          <stop offset="0" stop-color="#18b79a"/>
          <stop offset="0.55" stop-color="#3cc7ae"/>
          <stop offset="0.75" stop-color="#1a8fae"/>
          <stop offset="1" stop-color="#1a6f99"/>
        </linearGradient>
      </defs>
      <path d="M 40 196 C 250 240, 540 210, 612 0 C 560 200, 260 232, 40 196 Z"
            fill="url(#swooshGrad)" stroke="url(#swooshGrad)" stroke-width="5" stroke-linejoin="round"/>
    </svg>

    <span class="brand-name">velora</span>

    <div class="person">
      <p class="person-name">Daniel Hart</p>
      <p class="person-title">Manager</p>
    </div>

    <span class="divider"></span>

    <ul class="contact-list">
      <li class="contact-item">
        <svg class="contact-icon" viewBox="0 0 18 18" aria-hidden="true">
          <rect width="18" height="18" rx="4" fill="var(--teal)"/>
          <path d="M5.5 4.5 l2 0 l1 2.5 l-1.3 1 a6 6 0 0 0 2.8 2.8 l1-1.3 l2.5 1 l0 2 a1 1 0 0 1 -1 1 a9 9 0 0 1 -8-8 a1 1 0 0 1 1-1 z" fill="var(--card-navy)"/>
        </svg>
        <span>555-014-7320</span>
      </li>
      <li class="contact-item">
        <svg class="contact-icon" viewBox="0 0 18 18" aria-hidden="true">
          <rect width="18" height="18" rx="4" fill="var(--teal)"/>
          <rect x="3.5" y="5" width="11" height="8" rx="1" fill="none" stroke="var(--card-navy)" stroke-width="1.5"/>
          <path d="M3.5 5.5 L9 10 L14.5 5.5" fill="none" stroke="var(--card-navy)" stroke-width="1.5"/>
        </svg>
        <span>youremail@mailbox.com</span>
      </li>
      <li class="contact-item">
        <svg class="contact-icon" viewBox="0 0 18 18" aria-hidden="true">
          <rect width="18" height="18" rx="4" fill="var(--teal)"/>
          <circle cx="9" cy="9" r="5" fill="none" stroke="var(--card-navy)" stroke-width="1.4"/>
          <ellipse cx="9" cy="9" rx="2.2" ry="5" fill="none" stroke="var(--card-navy)" stroke-width="1.2"/>
          <line x1="4" y1="9" x2="14" y2="9" stroke="var(--card-navy)" stroke-width="1.2"/>
        </svg>
        <span>www.velora-app.com</span>
      </li>
    </ul>

    <p class="address">Your address, city, state, ZIP 0000</p>
  </section>

</main>
</body>
</html>
```